Business card design for Automotive workshop

We need a business card for a new automotive repair and tyre shop called Keelstone Prime Automotive located in New Zealand. We are a clean, modern and fresh workshop and company.

Front needs to feature logo,
my name:
Marlo Fenwicke (director)

Address:
48 Tarn Lane
Harrowford 3598

Phone: 07 594 2713
Mobile: 027 451 9362
Email: office@keelstoneautomotive.example.nz
Website: keelstoneautomotive.example.nz

Back needs to feature an area to write down appointment details, date and time.

Also feature a list of jobs and work we do such as,
Vehicle Servicing
All Mechanical Repairs
Warrant of Fitness
Tyres & Wheel Alignments
Automotive Diagnostics
Automotive Parts & Supplies

```html
<!DOCTYPE html>
<html lang="en">
<head>
<meta charset="utf-8">
<title>Keelstone Prime Automotive – Business Card</title>
<link href="https://fonts.googleapis.com/css2?family=Arimo:wght@400;700&display=swap" rel="stylesheet">
<style>
  :root{
    --stage-light:#4d4d4d;
    --stage-dark:#262626;
    --card-grey:#9c9ca0;
    --ink:#111111;
    --brand-red:#e3222a;
    --white:#ffffff;
    --black:#050505;
    --faint:#2b2424;
  }
  *{margin:0;padding:0;box-sizing:border-box}
  html,body{width:1200px;height:750px;overflow:hidden}
  body{
    position:relative;
    font-family:"Arimo",Arial,sans-serif;
    background:radial-gradient(ellipse 70% 60% at 50% 40%,var(--stage-light),var(--stage-dark));
  }
  .card{position:absolute;border-radius:32px;overflow:hidden;box-shadow:0 3px 8px rgba(0,0,0,.45)}
  .card-front{left:38px;top:186px;width:558px;height:328px;background:var(--card-grey);color:var(--ink)}
  .card-back{left:610px;top:187px;width:562px;height:328px;background:var(--black);color:var(--white)}

  /* front */
  .name-tag{position:absolute;left:0;top:70px;width:36px;height:30px;background:var(--brand-red)}
  .name-icon{position:absolute;left:21px;top:71px;width:28px;height:28px}
  .person-name{position:absolute;left:52px;top:72px;font-size:22px;font-weight:700;letter-spacing:.3px;word-spacing:3px}
  .person-role{position:absolute;left:46px;top:101px;font-size:19px;word-spacing:3px}

  .brand-pill{position:absolute;left:290px;top:138px;width:280px;height:51px;border-radius:26px 0 0 26px;background:var(--black);display:flex;align-items:center;padding-left:20px}
  .brand-name{color:var(--brand-red);font-weight:700;font-size:15.5px;letter-spacing:.4px;white-space:nowrap}

  .contact-list{list-style:none}
  .contact{position:absolute;left:0;height:16px;display:flex;align-items:center;font-size:14.5px;word-spacing:3px}
  .contact::before{content:"";position:absolute;left:0;top:0;width:32px;height:16px;background:var(--brand-red)}
  .contact svg{position:relative;margin-left:21px;width:17px;height:17px;flex:none}
  .contact span{margin-left:1px;white-space:nowrap}

  /* back */
  .back-brand{position:absolute;left:38px;top:70px;color:var(--brand-red);font-weight:700;font-size:17px;letter-spacing:.4px;white-space:nowrap}
  .back-brand-faint{position:absolute;left:318px;top:145px;color:var(--faint);font-weight:700;font-size:16px;letter-spacing:.4px;white-space:nowrap}
  .rail{position:absolute;left:19px;top:110px;width:16px;height:198px;border-radius:8px;background:var(--white)}
  .service-list{list-style:none}
  .service{position:absolute;left:37px;font-size:14.5px;word-spacing:3px;white-space:nowrap}
  .dot{position:absolute;width:8px;height:8px;border-radius:50%;background:var(--brand-red)}
  .appt-label{position:absolute;font-size:14.5px}
  .write-line{position:absolute;height:3px;background:var(--white)}
</style>
</head>
<body>

<section class="card card-front" aria-label="Card front">
  <div class="name-tag"></div>
  <svg class="name-icon" viewBox="0 0 28 28" aria-hidden="true">
    <circle cx="14" cy="14" r="13" fill="var(--brand-red)" stroke="var(--ink)" stroke-width="1"/>
    <circle cx="14" cy="14" r="9.5" fill="var(--ink)"/>
    <circle cx="14" cy="9" r="2" fill="var(--brand-red)"/>
    <rect x="12" y="12" width="4" height="8" rx="1" fill="var(--brand-red)"/>
  </svg>
  <h1 class="person-name">Marlo Fenwicke</h1>
  <p class="person-role">(Managing director)</p>

  <div class="brand-pill"><span class="brand-name">Keelstone Prime Automotive</span></div>

  <ul class="contact-list">
    <li class="contact" style="top:170px">
      <svg viewBox="0 0 18 18" aria-hidden="true"><circle cx="9" cy="9" r="8.5" fill="var(--ink)"/><path d="M6 4.5l2 2-1 1.3c.6 1.3 1.6 2.3 2.9 2.9l1.3-1 2 2-1.2 1.5C8.5 13 5 9.5 4.8 5.7z" fill="var(--brand-red)"/></svg>
      <span>027 451 9362</span>
    </li>
    <li class="contact" style="top:196px">
      <svg viewBox="0 0 18 18" aria-hidden="true"><circle cx="9" cy="9" r="8.5" fill="var(--ink)"/><path d="M4 8c0-2 10-2 10 0v1h-2.5V7.8H6.5V9H4z" fill="var(--brand-red)"/><rect x="5.5" y="9.5" width="7" height="3.5" rx="1" fill="var(--brand-red)"/></svg>
      <span>07 594 2713</span>
    </li>
    <li class="contact" style="top:220px">
      <svg viewBox="0 0 18 18" aria-hidden="true"><circle cx="9" cy="9" r="8.5" fill="var(--ink)"/><rect x="4.5" y="6" width="9" height="6.5" fill="var(--brand-red)"/><path d="M4.5 6l4.5 3.6L13.5 6" fill="none" stroke="var(--ink)" stroke-width="1"/></svg>
      <span>office@keelstoneautomotive.example.nz</span>
    </li>
    <li class="contact" style="top:242px">
      <svg viewBox="0 0 18 18" aria-hidden="true"><circle cx="9" cy="9" r="8.5" fill="var(--ink)"/><g fill="none" stroke="var(--brand-red)" stroke-width="1.1"><circle cx="9" cy="9" r="5"/><ellipse cx="9" cy="9" rx="2.2" ry="5"/><path d="M4 9h10"/></g></svg>
      <span>keelstoneautomotive.example.nz</span>
    </li>
    <li class="contact" style="top:268px">
      <svg viewBox="0 0 18 18" aria-hidden="true"><circle cx="9" cy="9" r="8.5" fill="var(--ink)"/><path d="M9 4l5 4.5h-1.5V13h-2.5v-3H8v3H5.5V8.5H4z" fill="var(--brand-red)"/></svg>
      <span>48 Tarn Lane Harrowford 3598</span>
    </li>
  </ul>
</section>

<section class="card card-back" aria-label="Card back">
  <div class="back-brand">Keelstone Prime Automotive</div>
  <div class="back-brand-faint" aria-hidden="true">Keelstone Prime Automotive</div>

  <div class="rail"></div>
  <ul class="service-list">
    <li><i class="dot" style="left:24px;top:130px"></i><span class="service" style="top:124px">Vehicle Servicing</span></li>
    <li><i class="dot" style="left:24px;top:155px"></i><span class="service" style="top:149px">All Mechanical Repairs</span></li>
    <li><i class="dot" style="left:24px;top:175px"></i><span class="service" style="top:169px">Warrant of Fitness</span></li>
    <li><i class="dot" style="left:24px;top:198px"></i><span class="service" style="top:192px">Tyres &amp; Wheel Alignments</span></li>
    <li><i class="dot" style="left:24px;top:223px"></i><span class="service" style="top:217px">Automotive Parts &amp; Supplies</span></li>
    <li><i class="dot" style="left:24px;top:247px"></i><span class="service" style="top:241px">Automotive Diagnostics</span></li>
  </ul>

  <i class="dot" style="left:25px;top:286px"></i>
  <span class="appt-label" style="left:37px;top:281px">Date</span>
  <div class="write-line" style="left:74px;top:292px;width:182px"></div>

  <i class="dot" style="left:290px;top:287px"></i>
  <span class="appt-label" style="left:302px;top:281px">Time</span>
  <div class="write-line" style="left:343px;top:292px;width:182px"></div>
</section>

</body>
</html>
```